Firm Stationery Design

I need a design for stationery, including: Stationery First Page, Stationery Second Sheet, Envelope, Mailing Label for Flat Envelopes, and Business Cards

```html
<!DOCTYPE html>
<html lang="en">
<head>
<meta charset="utf-8">
<title>Harlow Legal — Stationery Set</title>
<link rel="stylesheet" href="https://fonts.googleapis.com/css2?family=Montserrat:wght@700;800&family=Roboto:wght@400;500&family=Open+Sans:wght@400&display=swap">
<style>
  :root {
    --bg: #e7e8ea;
    --paper: #ffffff;
    --ink: #1d1d1b;
    --orange: #f7a21b;
    --orange-deep: #d98a12;
    --text: #4a4a4a;
    --rule: #3a3a3a;
    --faint: #ececec;
    --shadow: 0 2px 5px rgba(0,0,0,.18);
  }
  * { box-sizing: border-box; margin: 0; padding: 0; }
  html, body { width: 1200px; height: 992px; overflow: hidden; }
  body { background: var(--bg); font-family: "Roboto", Arial, sans-serif; color: var(--ink); position: relative; }
  .sheet { position: absolute; background: var(--paper); box-shadow: var(--shadow); }

  /* Brand lockup */
  .brand { display: flex; align-items: center; gap: 5px; font-family: "Montserrat", Arial, sans-serif; font-weight: 800; text-transform: uppercase; color: var(--ink); white-space: nowrap; line-height: 1; }
  .brand-mark { display: inline-block; background: var(--orange); flex: none; }
  .brand--light { color: #fff; }

  .icon { width: 7px; height: 7px; fill: var(--orange-deep); flex: none; }
  .contact-list { list-style: none; }
  .contact-list li { display: flex; align-items: center; gap: 4px; }

  /* Business card front */
  .card-front { left: 106px; top: 200px; width: 328px; height: 188px; }
  .card-front .brand { position: absolute; right: 38px; top: 62px; font-size: 17px; }
  .card-front .brand-mark { width: 11px; height: 11px; }
  .card-name { position: absolute; left: 34px; top: 96px; font-family: "Montserrat", Arial, sans-serif; font-weight: 700; font-size: 13px; letter-spacing: -.2px; }
  .card-title { position: absolute; left: 34px; top: 110px; font-size: 8.5px; color: var(--orange); }
  .card-rule { position: absolute; left: 97px; right: 34px; top: 115px; border-top: 1px solid var(--rule); }
  .card-front .contact-list { position: absolute; left: 34px; top: 128px; font-size: 9.5px; color: var(--ink); }
  .card-front .contact-list li { height: 12.5px; }
  .card-address { position: absolute; right: 34px; top: 130px; text-align: right; font-size: 9.5px; line-height: 12px; }

  /* Business card back */
  .card-back { left: 106px; top: 412px; width: 328px; height: 187px; }
  .card-back .pattern { position: absolute; inset: 0; background: linear-gradient(125deg, #8d8d8d 0%, #4a4a4a 35%, #1e1e1e 65%, #0e0e0e 100%); }
  .card-back .tile { position: absolute; left: 250px; top: 114px; width: 34px; height: 32px; background: #fff; display: flex; align-items: center; justify-content: center; font-family: "Montserrat", Arial, sans-serif; font-weight: 800; font-size: 6px; text-transform: uppercase; color: var(--ink); }

  /* Letterheads */
  .letter { top: 200px; width: 310px; height: 399px; }
  .letter--first { left: 462px; }
  .letter--second { left: 800px; }
  .letter .head { position: absolute; left: 32px; top: 30px; }
  .letter--first .head { font-size: 15px; }
  .letter--first .head .brand-mark { width: 14px; height: 14px; }
  .letter--second .head { font-size: 15px; }
  .letter--second .head .brand-mark { width: 9px; height: 9px; }
  .letter-body { position: absolute; left: 32px; top: 88px; width: 247px; font-family: "Open Sans", Arial, sans-serif; font-size: 4.6px; line-height: 6.45px; color: var(--text); }
  .letter-body p { margin-bottom: 6.5px; }
  .letter-body .salute { margin-bottom: 7px; }
  .signoff { position: absolute; left: 32px; top: 269px; font-family: "Open Sans", Arial, sans-serif; font-size: 4.6px; line-height: 6.6px; color: var(--text); }
  .signature { position: absolute; left: 32px; top: 291px; width: 24px; height: 23px; background: linear-gradient(135deg, #f4f4f4, #e2e2e2); }
  .letter-rule { position: absolute; left: 32px; right: 32px; top: 347px; border-top: 1px solid #9a9a9a; }
  .letter-rule::before { content: ""; position: absolute; left: 0; top: -1px; width: 9px; border-top: 1px solid var(--orange); }
  .letter .contact-list { position: absolute; left: 32px; top: 358px; font-size: 5.6px; line-height: 7.5px; color: var(--ink); }
  .letter .icon { width: 5px; height: 5px; }
  .letter-address { position: absolute; left: 118px; top: 359px; font-size: 5.6px; line-height: 7px; }
  .letter .foot-brand { position: absolute; right: 32px; top: 364px; font-size: 10px; }
  .letter .foot-brand .brand-mark { width: 7px; height: 7px; }

  /* Envelope back */
  .envelope-back { left: 106px; top: 629px; width: 349px; height: 163px; background: transparent; box-shadow: none; }
  .envelope-back svg.shape { position: absolute; inset: 0; filter: drop-shadow(0 2px 3px rgba(0,0,0,.18)); }
  .envelope-back .brand { position: absolute; left: 0; right: 0; top: 36px; justify-content: center; font-size: 9px; }
  .envelope-back .brand-mark { width: 7px; height: 7px; }

  /* Envelope front */
  .envelope-front { left: 473px; top: 629px; width: 348px; height: 163px; }
  .envelope-front .brand { position: absolute; left: 26px; top: 50px; font-size: 10.5px; }
  .envelope-front .brand-mark { width: 8px; height: 8px; }
  .return-address { position: absolute; left: 20px; top: 72px; width: 72px; text-align: center; font-size: 5.2px; line-height: 6.4px; color: var(--text); }
  .window { position: absolute; left: 24px; top: 112px; width: 81px; height: 32px; border-radius: 3px; background: linear-gradient(120deg, #c9c9c9 0%, #ececec 40%, #cfcfcf 70%, #bdbdbd 100%); }
  .envelope-front .backdrop { position: absolute; left: 182px; top: 8px; width: 148px; height: 146px; background: var(--faint); }

  /* Mailing label */
  .label { left: 846px; top: 629px; width: 238px; height: 160px; }
  .label-bar { position: absolute; left: 17px; top: 18px; width: 204px; height: 17px; background: var(--ink); color: #fff; font-size: 7.5px; font-weight: 500; display: flex; align-items: center; justify-content: center; letter-spacing: .2px; }
  .label-from { position: absolute; left: 17px; top: 43px; font-size: 8.5px; color: var(--text); }
  .label-line { position: absolute; left: 17px; width: 75px; border-top: 1px solid #777; }
  .label .brand { position: absolute; left: 17px; top: 126px; font-size: 9.5px; }
  .label .brand-mark { width: 8px; height: 8px; }
  .label-address { position: absolute; left: 106px; top: 92px; font-size: 8.8px; line-height: 10.5px; color: var(--ink); }
  .label-box { position: absolute; left: 106px; top: 135px; font-size: 8.8px; color: var(--ink); }
  .blank { display: inline-block; width: 32px; border-bottom: 1px solid var(--ink); margin: 0 2px; }
</style>
</head>
<body>
<svg width="0" height="0" style="position:absolute" aria-hidden="true">
  <symbol id="i-phone" viewBox="0 0 10 10"><path d="M1 3c0-1 1-2 4-2s4 1 4 2v1H7V3H3v1H1zM2 5h6l1 4H1z"/></symbol>
  <symbol id="i-mail" viewBox="0 0 10 10"><path d="M0 2h10v1L5 6 0 3zM0 4l5 3 5-3v4H0z"/></symbol>
  <symbol id="i-globe" viewBox="0 0 10 10"><circle cx="5" cy="5" r="4.5"/><path d="M3 3h3v2H4zM6 6h2v1H6z" fill="#fff"/></symbol>
</svg>

<!-- Business card, front -->
<section class="sheet card-front" aria-label="Business card front">
  <div class="brand"><span class="brand-mark"></span><span class="brand-name">Harlow Legal</span></div>
  <h2 class="card-name">DANA ORTIZ</h2>
  <p class="card-title">Founder &amp; CEO</p>
  <div class="card-rule"></div>
  <ul class="contact-list">
    <li><svg class="icon"><use href="#i-phone"/></svg>(555) 214-7730</li>
    <li><svg class="icon"><use href="#i-mail"/></svg>hello@harlowlegal.com</li>
    <li><svg class="icon"><use href="#i-globe"/></svg>www.harlowlegal.com</li>
  </ul>
  <p class="card-address">480 Cedar Lane Suite 12,<br>Brookfield,<br>60513 Illinois / USA</p>
</section>

<!-- Business card, back -->
<section class="sheet card-back" aria-label="Business card back">
  <div class="pattern" role="img" aria-label="Embossed dark repeating pattern fading from silver to black"></div>
  <div class="tile">Harlow</div>
</section>

<!-- Letterhead, first page -->
<section class="sheet letter letter--first" aria-label="Letterhead first page">
  <div class="head brand"><span class="brand-mark"></span><span class="brand-name">Harlow Legal</span></div>
  <div class="letter-body">
    <p class="salute">Dear customer,</p>
    <p>Thank you for choosing our firm. This letter confirms the scope of the work we discussed and outlines the documents we will need from you. Our team will review each item with care and keep you informed at every stage of the process. Please sign and return the enclosed forms at your earliest convenience. If any detail seems unclear, call our office and a member of staff will gladly walk you through it. We value your trust and look forward to a good result together.</p>
    <p>Please sign and return the enclosed forms at your earliest convenience. If any detail seems unclear, call our office and a member of staff will gladly walk you through it. We value your trust and look forward to a good result together. Thank you for choosing our firm. This letter confirms the scope of the work we discussed and outlines the documents we will need from you. Our team will review each item with care and keep you informed at every stage of the process.</p>
    <p>Thank you for choosing our firm. This letter confirms the scope of the work we discussed and outlines the documents we will need from you. Our team will review each item with care and keep you informed at every stage of the process. Please sign and return the enclosed forms at your earliest convenience. If any detail seems unclear, call our office and a member of staff will gladly walk you through it. We value your trust and look forward to a good result together.</p>
    <p>Thank you for choosing our firm. This letter confirms the scope of the work we discussed and outlines the documents we will need from you. Our team will review each item with care and keep you informed at every stage of the process.</p>
    <p>Yours Sincerely,</p>
  </div>
  <p class="signoff">Paul Reyes<br>General Director</p>
  <div class="signature" role="img" aria-label="Handwritten signature"></div>
  <div class="letter-rule"></div>
  <ul class="contact-list">
    <li><svg class="icon"><use href="#i-phone"/></svg>(555) 214-7730</li>
    <li><svg class="icon"><use href="#i-mail"/></svg>hello@harlowlegal.com</li>
    <li><svg class="icon"><use href="#i-globe"/></svg>www.harlowlegal.com</li>
  </ul>
  <p class="letter-address">480 Cedar Lane Suite 12,<br>Brookfield,<br>60513 Illinois / USA</p>
  <div class="foot-brand brand"><span class="brand-name">Harlow Legal</span></div>
</section>

<!-- Letterhead, second sheet -->
<section class="sheet letter letter--second" aria-label="Letterhead second sheet">
  <div class="head brand"><span class="brand-name">Harlow Legal</span></div>
  <div class="letter-body">
    <p class="salute">Dear customer,</p>
    <p>Thank you for choosing our firm. This letter confirms the scope of the work we discussed and outlines the documents we will need from you. Our team will review each item with care and keep you informed at every stage of the process. Please sign and return the enclosed forms at your earliest convenience. If any detail seems unclear, call our office and a member of staff will gladly walk you through it. We value your trust and look forward to a good result together.</p>
    <p>Please sign and return the enclosed forms at your earliest convenience. If any detail seems unclear, call our office and a member of staff will gladly walk you through it. We value your trust and look forward to a good result together. Thank you for choosing our firm. This letter confirms the scope of the work we discussed and outlines the documents we will need from you. Our team will review each item with care and keep you informed at every stage of the process.</p>
    <p>Thank you for choosing our firm. This letter confirms the scope of the work we discussed and outlines the documents we will need from you. Our team will review each item with care and keep you informed at every stage of the process. Please sign and return the enclosed forms at your earliest convenience. If any detail seems unclear, call our office and a member of staff will gladly walk you through it. We value your trust and look forward to a good result together.</p>
    <p>Thank you for choosing our firm. This letter confirms the scope of the work we discussed and outlines the documents we will need from you. Our team will review each item with care and keep you informed at every stage of the process.</p>
    <p>Yours Sincerely,</p>
  </div>
  <p class="signoff">Paul Reyes<br>General Director</p>
  <div class="signature" role="img" aria-label="Handwritten signature"></div>
  <div class="letter-rule"></div>
  <ul class="contact-list">
    <li><svg class="icon"><use href="#i-phone"/></svg>(555) 214-7730</li>
    <li><svg class="icon"><use href="#i-mail"/></svg>hello@harlowlegal.com</li>
    <li><svg class="icon"><use href="#i-globe"/></svg>www.harlowlegal.com</li>
  </ul>
  <p class="letter-address">480 Cedar Lane Suite 12,<br>Brookfield,<br>60513 Illinois / USA</p>
  <div class="foot-brand brand"><span class="brand-mark"></span></div>
</section>

<!-- Envelope, back -->
<section class="sheet envelope-back" aria-label="Envelope back">
  <svg class="shape" width="349" height="163" viewBox="0 0 349 163">
    <path d="M0 0H349V163H0Z" fill="#fff"/>
    <path d="M10 30 L6 159 M339 30 L343 159" stroke="#c8c8c8" stroke-width="1" fill="none"/>
    <path d="M0 0 H349 L327 50 Q322 60 310 60 H39 Q27 60 22 50 Z" fill="#1d1d1b"/>
  </svg>
  <div class="brand brand--light"><span class="brand-mark"></span><span class="brand-name">Harlow Legal</span></div>
</section>

<!-- Envelope, front -->
<section class="sheet envelope-front" aria-label="Envelope front">
  <div class="brand"><span class="brand-mark"></span><span class="brand-name">Harlow</span></div>
  <p class="return-address">72 Elm Street, Suite 4<br>Milton, VT 05468</p>
  <div class="window"></div>
  <div class="backdrop"></div>
</section>

<!-- Mailing label -->
<section class="sheet label" aria-label="Mailing label">
  <div class="label-bar">MAILING LABEL</div>
  <p class="label-from">FROM</p>
  <div class="label-line" style="top:62px"></div>
  <div class="label-line" style="top:72px"></div>
  <div class="label-line" style="top:83px"></div>
  <div class="brand"><span class="brand-mark"></span><span class="brand-name">Harlow</span></div>
  <p class="label-address">480 Cedar Lane Suite 12,<br>Brookfield,<br>60513 Illinois / USA</p>
  <p class="label-box">BOX<span class="blank"></span>OF<span class="blank" style="width:27px"></span></p>
</section>
</body>
</html>
```